Roofing Company Modern look

I want a modern and sophisticated look for our roofing business.

Our address is :

5217 Mallow Creek Ln
Orlando, Fl 32825

(407)-583-2196

www.HarborlineRoofsFl.com

I also want to make sure on the back there is a spot to put
Project Manager Name :

Number:

Because the cards will be used by all sales people

Project Manager Name :

Also there are accreditation we have logos are uploaded here as well that I would like maybe on the back of card as well

I also want to highlight our special attributions or trades:

Residential & Commercial
Fully Insured
License # CCC7482913
Insurance Claims
Serving Central Florida Since 1992
Free Estimates

Contact Information for Business Card

Our address is :

5217 Mallow Creek Ln
Orlando, Fl 32825

(407)-583-2196

Project Manager Name :

Residential & Commercial
Fully Insured
License # CCC7482913
Insurance Claims
Free Estimates

Font styles to use
Serif
Sans Serif

Colors
3176b5

Requirements
Must have
• Must have royal blue like my logo grey and black are the colors I like

```html
<!DOCTYPE html>
<html lang="en">
<head>
<meta charset="utf-8">
<title>Harborline Roofing &amp; Gutters Inc. – Business Card</title>
<link href="https://fonts.googleapis.com/css2?family=Michroma&family=Questrial&display=swap" rel="stylesheet">
<style>
  :root {
    --page-bg: #e6e6e6;
    --card-bg: #ffffff;
    --brand-blue: #3176b5;
    --brand-blue-deep: #1f5f99;
    --text-dark: #333333;
    --text-grey: #555555;
    --badge-grey: #8a8f95;
    --badge-navy: #1e3a6b;
  }
  * { box-sizing: border-box; margin: 0; padding: 0; }
  html, body { width: 1200px; height: 1200px; overflow: hidden; }
  body {
    background: var(--page-bg);
    font-family: "Questrial", "Century Gothic", sans-serif;
    color: var(--text-dark);
    position: relative;
  }
  .card {
    position: absolute;
    left: 257px;
    width: 686px;
    height: 392px;
    background: var(--card-bg);
    border-radius: 26px;
    box-shadow: 0 10px 24px rgba(0,0,0,0.18);
  }
  .card--front { top: 158px; }
  .card--back { top: 650px; }

  /* Front */
  .brand {
    position: absolute;
    top: 78px;
    left: 0;
    width: 100%;
    text-align: center;
  }
  .brand__mark {
    width: 92px;
    height: 92px;
    border-radius: 50%;
    background: var(--brand-blue);
    margin: 0 auto 18px;
  }
  .brand__name {
    font-family: "Michroma", sans-serif;
    font-size: 36px;
    letter-spacing: 2px;
    color: var(--brand-blue);
    line-height: 1;
  }
  .brand__tagline {
    font-family: "Michroma", sans-serif;
    font-size: 13px;
    letter-spacing: 3px;
    color: var(--text-grey);
    margin-top: 10px;
  }
  .contact {
    position: absolute;
    top: 304px;
    left: 0;
    width: 100%;
    text-align: center;
    font-size: 18px;
    color: var(--text-dark);
  }
  .contact__row {
    display: flex;
    justify-content: center;
    align-items: center;
    gap: 4px;
  }
  .contact__divider {
    width: 402px;
    height: 1px;
    background: var(--brand-blue);
    margin: 5px auto 6px;
  }
  .contact__item { display: inline-flex; align-items: center; gap: 4px; margin: 0 2px; }
  .icon { width: 18px; height: 18px; flex: none; }

  /* Back */
  .field {
    position: absolute;
    left: 51px;
    width: 581px;
    display: flex;
    align-items: flex-end;
    color: var(--brand-blue-deep);
    font-size: 16px;
  }
  .field--name { top: 56px; }
  .field--phone { top: 114px; }
  .field__line {
    flex: 1;
    border-bottom: 1px solid var(--brand-blue);
    margin-left: 2px;
    margin-bottom: 4px;
  }
  .services {
    position: absolute;
    top: 176px;
    list-style: none;
    font-size: 17px;
    color: var(--text-dark);
    line-height: 19.5px;
  }
  .services--left { left: 51px; }
  .services--right { left: 338px; }
  .services li { display: flex; align-items: center; gap: 10px; }
  .services li::before {
    content: "";
    width: 9px;
    height: 9px;
    border-radius: 50%;
    background: var(--brand-blue);
    flex: none;
  }
  .badges { position: absolute; top: 0; left: 0; width: 100%; height: 100%; pointer-events: none; }
  .badge { position: absolute; }
  .badge--rating { left: 49px; top: 281px; width: 46px; height: 57px; border: 2px solid var(--brand-blue-deep); border-radius: 5px; background: #eef3f9; }
  .badge--applicator { left: 190px; top: 282px; width: 64px; height: 56px; background: var(--badge-navy); clip-path: polygon(50% 0, 100% 25%, 100% 75%, 50% 100%, 0 75%, 0 25%); }
  .badge--contractor { left: 346px; top: 291px; width: 136px; height: 38px; border: 2px solid var(--badge-navy); background: #c8202a; }
  .badge--listing { left: 574px; top: 284px; width: 58px; height: 52px; border-radius: 50%; border: 4px solid var(--badge-grey); background: #f3f3f3; }
</style>
</head>
<body>

<section class="card card--front" aria-label="Business card front">
  <div class="brand">
    <div class="brand__mark"></div>
    <div class="brand__name">HARBORLINE</div>
    <div class="brand__tagline">ROOFING &amp; GUTTERS INC.</div>
  </div>
  <div class="contact">
    <div class="contact__row">
      <svg class="icon" viewBox="0 0 20 20" aria-hidden="true"><circle cx="10" cy="10" r="10" fill="#3176b5"/><path d="M10 4a4 4 0 0 0-4 4c0 3 4 8 4 8s4-5 4-8a4 4 0 0 0-4-4z" fill="#fff"/><circle cx="10" cy="8" r="1.6" fill="#3176b5"/></svg>
      <span>5217 Mallow Creek Ln, Orlando, Fl 32825</span>
    </div>
    <div class="contact__divider"></div>
    <div class="contact__row">
      <span class="contact__item">
        <svg class="icon" viewBox="0 0 20 20" aria-hidden="true"><circle cx="10" cy="10" r="10" fill="#1f5f99"/><path d="M7 5l2 2.4-1.2 1.4a7 7 0 0 0 3.4 3.4l1.4-1.2 2.4 2-1.2 1.6c-4 0-8-4-8-8z" fill="#fff"/></svg>
        (407)-583-2196
      </span>
      <span class="contact__item">
        <svg class="icon" viewBox="0 0 20 20" aria-hidden="true"><circle cx="10" cy="10" r="10" fill="#3176b5"/><circle cx="10" cy="10" r="5.5" fill="none" stroke="#fff" stroke-width="1.1"/><ellipse cx="10" cy="10" rx="2.4" ry="5.5" fill="none" stroke="#fff" stroke-width="1.1"/><path d="M4.5 10h11" stroke="#fff" stroke-width="1.1"/></svg>
        www.HarborlineRoofsFl.com
      </span>
    </div>
  </div>
</section>

<section class="card card--back" aria-label="Business card back">
  <div class="field field--name"><span>NAME:</span><span class="field__line"></span></div>
  <div class="field field--phone"><span>PHONE:</span><span class="field__line"></span></div>

  <ul class="services services--left">
    <li>Residential &amp; Commercial</li>
    <li>Fully Insured</li>
    <li>License # CCC7482913</li>
  </ul>
  <ul class="services services--right">
    <li>Insurance Claims</li>
    <li>Serving Central Florida Since 1992</li>
    <li>Free Estimates</li>
  </ul>

  <div class="badges">
    <div class="badge badge--rating" role="img" aria-label="Accreditation rating badge"></div>
    <div class="badge badge--applicator" role="img" aria-label="Shingle applicator certification badge"></div>
    <div class="badge badge--contractor" role="img" aria-label="Authorized roofing contractor badge"></div>
    <div class="badge badge--listing" role="img" aria-label="Screened and approved listing badge"></div>
  </div>
</section>

</body>
</html>
```